Forensic Document Examiner, looking for contemporary update to my stationery design.

Looking for professional, classy logo design for stationery and business cards. My current stationery and business card is attached.I believe a logo image makes a header section interesting, so an intriguing design of a pen, feathered pen, microscope, magnifying glass, etc., would be appropriate. I have been in the business for over 30 years. I leave ideas to the imagination of the designer.My work involves mainly, the comparison of signatures and handwriting. I also resolve alterations, obliterations, and work as shown on my website: www.documentexaminer.infoThe image produced will be printed on quality white stationery and envelopes. The stationery will be photocopied by my clients, so the images should be reproducible. The business cards may be designed in other than white.

Target Market(s)

Attorneys

Font styles to use
Sans Serif

Colors

Designer to choose colors to be used in the design.

Requirements
Must have
• Image suitable for white stationery and photocopying.
• Classy logo and image; no casual fonts.
Nice to have
• Intriguing, contemporary design incorporating a relevant logo to my work.

```html
<!DOCTYPE html>
<html lang="en">
<head>
<meta charset="utf-8">
<title>Marcus D. Hale Stationery</title>
<link href="https://fonts.googleapis.com/css2?family=Didact+Gothic&family=Open+Sans:wght@400;600&display=swap" rel="stylesheet">
<style>
  :root {
    --backdrop: #dcdcdc;
    --paper: #f6f6f6;
    --ink: #3a3a3a;
    --body-ink: #555555;
    --brand: #2f2f9c;
    --rule: #333333;
    --flap-line: #e6e6e6;
  }
  * { margin: 0; padding: 0; box-sizing: border-box; }
  html, body { width: 1200px; height: 877px; overflow: hidden; background: var(--backdrop); }
  .canvas { position: relative; width: 1200px; height: 877px; }
  .sheet { position: absolute; background: var(--paper); }

  .letterhead { left: 59px; top: 66px; width: 527px; height: 742px; }
  .brand-lockup {
    position: absolute; left: 0; right: 0; top: 42px;
    display: flex; align-items: center; justify-content: center; gap: 6px;
    font-family: "Open Sans", sans-serif; font-weight: 600; color: var(--brand);
  }
  .brand-dot { width: 12px; height: 12px; border-radius: 50%; background: var(--brand); }
  .brand-name { font-size: 19px; letter-spacing: 1px; line-height: 1; }
  .contact-bar {
    position: absolute; left: 45px; width: 440px; top: 100px; height: 15px;
    border-top: 1px solid var(--rule); border-bottom: 1px solid var(--rule);
    font-family: "Open Sans", sans-serif; font-size: 7.6px; color: var(--ink);
    display: flex; align-items: center; justify-content: center; white-space: nowrap;
  }
  .contact-bar span + span::before { content: "|"; margin: 0 4px; }

  .letter { position: absolute; left: 45px; width: 440px; top: 207px; font-family: "Didact Gothic", sans-serif; color: var(--body-ink); }
  .salutation { font-size: 13.5px; color: var(--ink); margin-bottom: 24px; }
  .letter p.body { font-size: 7.1px; line-height: 11.4px; text-align: justify; margin-bottom: 11px; }
  .closing { font-size: 7.1px; margin-top: 22px; }
  .signature { display: block; margin-top: 8px; width: 62px; height: 26px; background: linear-gradient(180deg, transparent 40%, #c9ccd3 50%, transparent 62%); }

  .envelope-back { left: 620px; top: 293px; width: 530px; height: 239px; }
  .flap { position: absolute; left: 14px; right: 10px; top: 0; height: 71px; border: 1.5px solid var(--flap-line); border-top: none; border-radius: 0 0 16px 16px; }
  .flap-mark { position: absolute; left: 0; right: 0; top: 28px; text-align: center; font-family: "Open Sans", sans-serif; font-weight: 600; font-size: 10px; letter-spacing: 1px; color: var(--brand); }

  .envelope-front { left: 620px; top: 566px; width: 532px; height: 242px; }
  .envelope-front .brand-lockup { left: 33px; right: auto; top: 30px; justify-content: flex-start; }
</style>
</head>
<body>
<div class="canvas">
  <section class="sheet letterhead">
    <div class="brand-lockup">
      <span class="brand-dot"></span>
      <span class="brand-name">MARCUS D. HALE</span>
    </div>
    <div class="contact-bar">
      <span>(555) 210-4476</span><span>mhale@quillmarkreview.info</span><span>www.quillmarkreview.info</span><span>P.O.Box 8124, Salem, OR 97301</span>
    </div>
    <div class="letter">
      <p class="salutation">Dear Mr. Carter,</p>
      <p class="body">Lorem ipsum dolor sit amet, consectetur adipiscing elit. Donec orci purus, luctus vitae dignissim eu, iaculis sed purus. Vivamus faucibus, ipsum nec aliquet viverra, leo mauris condimentum ligula, sit amet sagittis enim ligula quis arcu. Nam egestas tortor id nisi porttitor mattis. In tortor ante, ultricies in suscipit a, tempus non massa. Vivamus et auctor mi. Fusce vel massa nulla. Phasellus nec eros mauris, et scelerisque orci.</p>
      <p class="body">Donec malesuada orci vitae nulla accumsan porta a id massa. Quisque accumsan iaculis magna sit amet fringilla. Maecenas consequat, magna eget tincidunt semper, odio nibh rutrum mi, id feugiat ante nisi eu risus. Vestibulum nunc orci, rhoncus a placerat in, ultricies in mi. Cras mattis varius eros, vel fringilla nisi suscipit eget. Quisque scelerisque sagittis nulla at porttitor.</p>
      <p class="body">Sed id augue vitae urna euismod commodo aliquet a quam. Pellentesque arcu velit, cursus et malesuada ut, consequat et diam. Nullam erat sem, rhoncus id ullamcorper vitae, rhoncus et arcu. In ultricies ultricies nulla, ut rutrum nisi iaculis at. Donec eu magna a metus ornare faucibus. Fusce aliquet faucibus ultricies. Morbi semper, est id tincidunt gravida, sem arcu adipiscing lacus, ac bibendum nulla leo eu purus. Quisque nec diam sed risus consectetur a ccumsan quis quis nibh. Vestibulum id purus lorem.</p>
      <p class="body">It is a long established fact that a reader will be distracted by the readable content of a page when looking at its layout. The point of using Lorem Ipsum is that it has a more-or-less normal distribution of letters, as opposed to using 'Content here, content here', making it look like readable English. Many desktop publishing packages</p>
      <p class="closing">Sincerely,</p>
      <span class="signature" role="img" aria-label="Handwritten signature"></span>
    </div>
  </section>

  <section class="sheet envelope-back">
    <div class="flap"></div>
    <div class="flap-mark">MARCUS D. HALE</div>
  </section>

  <section class="sheet envelope-front">
    <div class="brand-lockup">
      <span class="brand-dot"></span>
      <span class="brand-name">MARCUS D. HALE</span>
    </div>
  </section>
</div>
</body>
</html>
```